business card - Helicopter Flight Services, Flight School, etc.

We need a business card design for a new helicopter service.

We offer Helicopter Flight Services, Aerial Filming & Photography, Flight School, and Helicopter Tours. In that order.

Summit BladeAir, Inc.
Dennis Tollerby
SummitBladeair@Kestmail.com
626-418-7352

Based at the Brenwick Airport in Van Nuys, CA. The final design should communicate integrity and safety. Pictures or logos at your discretion.

Card back side - surprise me.

```html
<!DOCTYPE html>
<html lang="en">
<head>
<meta charset="utf-8">
<title>Summit BladeAir, Inc. — Business Card</title>
<link rel="stylesheet" href="https://fonts.googleapis.com/css2?family=Open+Sans:wght@400;600;700&display=swap">
<style>
  :root {
    --sky: #0a93f5;
    --sky-text: #1a8ae6;
    --sky-faint: rgba(255, 255, 255, 0.10);
    --paper: #ffffff;
    --ink: #1c1c1c;
    --stage: #e9ecef;
    --shadow: rgba(0, 0, 0, 0.18);
  }
  * { box-sizing: border-box; margin: 0; padding: 0; }
  html, body {
    width: 1200px;
    height: 900px;
    overflow: hidden;
    background: var(--stage);
    font-family: "Open Sans", sans-serif;
  }
  .canvas {
    position: relative;
    width: 1200px;
    height: 900px;
  }
  .card {
    position: absolute;
    width: 630px;
    height: 360px;
    overflow: hidden;
    box-shadow: 0 10px 24px var(--shadow);
  }

  /* Back side */
  .card-back {
    left: 90px;
    top: 90px;
    background: var(--sky);
    color: var(--paper);
  }
  .back-emblem {
    position: absolute;
    left: -110px;
    top: -60px;
    width: 340px;
    height: 340px;
    border-radius: 50%;
    background: var(--sky-faint);
  }
  .services {
    position: absolute;
    top: 40px;
    left: 310px;
    list-style: none;
    font-size: 15px;
    line-height: 28px;
  }
  .services li {
    display: flex;
    align-items: center;
    gap: 10px;
  }
  .services li::before {
    content: "";
    width: 8px;
    height: 8px;
    border-radius: 50%;
    background: var(--paper);
    flex: none;
  }
  .services li:nth-child(2) { padding-left: 12px; }
  .services li:nth-child(3) { padding-left: 24px; }
  .services li:nth-child(4) { padding-left: 36px; }
  .back-wordmark {
    position: absolute;
    left: 40px;
    bottom: 38px;
    font-weight: 600;
    font-size: 20px;
    letter-spacing: 2px;
    text-transform: uppercase;
    line-height: 1.2;
    text-align: center;
  }

  /* Front side */
  .card-front {
    left: 480px;
    top: 470px;
    background: var(--paper);
    color: var(--ink);
  }
  .contact {
    position: absolute;
    left: 330px;
    top: 44px;
  }
  .contact-name {
    color: var(--sky-text);
    font-weight: 700;
    font-size: 18px;
    margin-bottom: 20px;
  }
  .contact-line {
    display: flex;
    align-items: center;
    gap: 10px;
    font-size: 13.5px;
    line-height: 24px;
  }
  .contact-line svg { flex: none; }
  .front-brand {
    position: absolute;
    left: 40px;
    bottom: 44px;
    display: flex;
    align-items: center;
    gap: 20px;
  }
  .brand-dot {
    width: 96px;
    height: 96px;
    border-radius: 50%;
    background: var(--sky-text);
    flex: none;
  }
  .brand-name {
    color: var(--sky-text);
    font-weight: 600;
    font-size: 26px;
    line-height: 1.25;
    letter-spacing: 2px;
    text-transform: uppercase;
    text-align: center;
  }
</style>
</head>
<body>
<main class="canvas">

  <section class="card card-back" aria-label="Card back">
    <span class="back-emblem" aria-hidden="true"></span>
    <ul class="services">
      <li>Helicopter Flight Services</li>
      <li>Aerial Filming &amp; Photography</li>
      <li>Flight School</li>
      <li>Helicopter Tours</li>
    </ul>
    <p class="back-wordmark">Summit BladeAir<br>Inc.</p>
  </section>

  <section class="card card-front" aria-label="Card front">
    <div class="contact">
      <p class="contact-name">Dennis Tollerby</p>
      <p class="contact-line">
        <svg width="12" height="12" viewBox="0 0 24 24" aria-hidden="true">
          <path fill="#1a8ae6" d="M6.6 10.8a15.1 15.1 0 0 0 6.6 6.6l2.2-2.2a1 1 0 0 1 1-.25 11.4 11.4 0 0 0 3.6.57 1 1 0 0 1 1 1V20a1 1 0 0 1-1 1A17 17 0 0 1 3 4a1 1 0 0 1 1-1h3.5a1 1 0 0 1 1 1c0 1.25.2 2.45.57 3.6a1 1 0 0 1-.25 1z"/>
        </svg>
        <span>626-418-7352</span>
      </p>
      <p class="contact-line">
        <svg width="12" height="10" viewBox="0 0 24 18" aria-hidden="true">
          <rect x="0" y="0" width="24" height="18" rx="2" fill="#1a8ae6"/>
          <path d="M1 2l11 8 11-8" fill="none" stroke="#ffffff" stroke-width="2"/>
        </svg>
        <span>SummitBladeair@Kestmail.com</span>
      </p>
    </div>
    <div class="front-brand">
      <span class="brand-dot" aria-hidden="true"></span>
      <p class="brand-name">Summit BladeAir<br>Inc.</p>
    </div>
  </section>

</main>
</body>
</html>
```